Banner to be displayed at local Farmers Market Booth.

Graphic Design Brief: Farmers Market Banner Contest

Project Overview:We are seeking talented graphic designers to create a visually appealing banner for our booth at the local farmers market. Our company specializes in healthy, all-natural dog and cat treats, and we want a banner that captures our brand identity while drawing in pet owners who value quality and nutrition for their furry friends.

Banner Specifications:

Size: 24 inches x 60 inches (Horizontal orientation) 24" High X 60 wide

Theme: Vintage/Retro

Style: Warm, inviting, nostalgic with a touch of rustic charm

Colors: Earthy, muted tones such as warm browns, soft greens, and creamy yellows. Pops of red or blue may be used sparingly for accents. OR Black and White with gray scales. Would like to see both

Typography: Retro-style fonts that are readable and align with the vintage aesthetic.

Key Elements to Include: website (www.moltbyfarms.com)

Company Name: Moltby Farms

Tagline: " Simply Honest Bites "
Imagery: Illustrations or stylized graphics of happy dogs and cats, possibly interacting with treats.

Emphasis on Natural Ingredients: Icons or design elements that subtly suggest freshness and quality (e.g., leaves, wheat, bones, or paw prints).

Farmers Market Appeal: A design that blends well with the artisanal, handmade, and farm-fresh atmosphere of the market.

Design Considerations:

The banner should be easily readable from a distance.

A balanced composition that doesn't feel overcrowded.

Should evoke trust and warmth while maintaining a professional look.

Avoid overly modern or sleek elements that don’t align with the vintage aesthetic.

Submission Requirements:

High-resolution digital file in PDF or AI format.

CMYK color mode for printing purposes.

Must include a mockup or preview of how it would look in a real farmers market setting.

We look forward to seeing your creative interpretations of our brand! If you have any questions, feel free to reach out.

Font styles to use
Other font styles liked:
• See attachement

Requirements
Nice to have
• Retro/Vintage,playful BUT NOT whimsical

```html
<!DOCTYPE html>
<html lang="en">
<head>
<meta charset="utf-8">
<title>Moltby Farms Banner</title>
<link href="https://fonts.googleapis.com/css2?family=Black+Ops+One&family=Cinzel:wght@600;700;900&display=swap" rel="stylesheet">
<style>
  :root {
    --page: #e9e6e1;
    --ink: #141414;
    --chalk: #f2efe9;
    --orange: #e5782d;
    --orange-dark: #c9621f;
    --shadow: #1a1a1a;
  }
  * { margin: 0; padding: 0; box-sizing: border-box; }
  html, body {
    width: 1200px; height: 944px; overflow: hidden;
    background: var(--page);
  }
  .banner {
    position: absolute; left: 40px; top: 248px;
    width: 1120px; height: 448px;
    background: var(--ink);
    overflow: hidden;
  }
  .banner__band {
    position: absolute; left: 0; top: 0; width: 1120px; height: 448px;
  }
  .brand-name {
    position: absolute; left: 48px; top: 44px; width: 650px;
    font-family: "Black Ops One", system-ui, sans-serif;
    font-weight: 400;
    color: var(--chalk);
    text-align: center;
    line-height: 0.98;
    letter-spacing: 3px;
  }
  .brand-name__line { display: block; font-size: 92px; }
  .website {
    position: absolute; left: 48px; top: 238px; width: 650px;
    text-align: center;
    font-family: "Cinzel", Georgia, serif;
    font-weight: 600;
    font-size: 26px;
    line-height: 1;
    letter-spacing: 3px;
    color: var(--chalk);
  }
  .tagline {
    position: absolute; left: 50px; top: 328px;
    font-family: "Cinzel", Georgia, serif;
    font-weight: 900;
    font-size: 46px;
    line-height: 1;
    letter-spacing: 3px;
    color: var(--chalk);
    text-shadow: -3px 3px 0 var(--shadow);
    white-space: nowrap;
  }
  .descriptor {
    position: absolute; left: 50px; top: 390px;
    font-family: "Cinzel", Georgia, serif;
    font-weight: 700;
    font-size: 40px;
    line-height: 1;
    letter-spacing: 0.5px;
    color: var(--chalk);
    white-space: nowrap;
  }
  .pet-illustration {
    position: absolute; left: 720px; top: 58px;
    width: 280px; height: 322px;
    border-radius: 40px 40px 12px 12px;
    background: linear-gradient(160deg, #d9d6d0 0%, #8d8a85 60%, #3a3a3a 100%);
  }
  .market-mark {
    position: absolute; left: 1012px; top: 66px;
    display: flex; align-items: center; gap: 6px;
    font-family: "Cinzel", Georgia, serif;
    font-weight: 700;
    font-size: 20px;
    line-height: 1;
    color: var(--chalk);
  }
  .market-mark__dot {
    width: 12px; height: 12px; border-radius: 50%;
    background: var(--chalk);
  }
</style>
</head>
<body>
  <section class="banner">
    <svg class="banner__band" viewBox="0 0 1120 448" aria-hidden="true">
      <polygon fill="var(--orange)"
        points="0,275 40,282 70,268 110,280 150,270 190,290 240,272 280,284 320,262 360,278 400,266 440,286 480,274 520,292 560,270 600,284 640,262 680,280 720,268 760,288 800,272 840,284 880,264 920,282 960,270 1000,290 1040,272 1080,284 1120,268 1120,448 0,448"/>
      <polyline fill="none" stroke="var(--chalk)" stroke-width="3"
        points="0,275 40,282 70,268 110,280 150,270 190,290 240,272 280,284 320,262 360,278 400,266 440,286 480,274 520,292 560,270 600,284 640,262 680,280 720,268 760,288 800,272 840,284 880,264 920,282 960,270 1000,290 1040,272 1080,284 1120,268"/>
      <rect x="0" y="440" width="1120" height="8" fill="var(--orange-dark)"/>
    </svg>

    <h1 class="brand-name">
      <span class="brand-name__line">MOLTBY</span>
      <span class="brand-name__line">FARMS</span>
    </h1>
    <p class="website">WWW.MOLTBYFARMS.COM</p>

    <div class="pet-illustration" role="img" aria-label="Illustration of a puppy and a kitten sitting side by side"></div>

    <div class="market-mark">
      <span class="market-mark__dot"></span>
      <span>Moltby</span>
    </div>

    <p class="tagline">SIMPLY HONEST BITES</p>
    <p class="descriptor">PURVEYORS OF PREMIUM PET FOOD &amp; TREATS</p>
  </section>
</body>
</html>
```